Website Update for Global Company - Solar Technology - LeafCore

We recently released our first version of our website velirox.com. However despite a longer process of developing the page, it is still missing the elements of a brilliant website. (Currently it looks dead and boring) We are having problems integrating our logo and want to create a more catching site. The task involves an updated and without changing most of main elements in the existing page. (Unless you can do it even better) The blue color needs to be kept but can be changed within the blue-spectrum. The logo text (VELIROX) must be better integrated in the site, however the main logo could be used in elements like we have tried with the background. The surface of the logo could be changed to 3D or metallic, or any other theme that would make the site more complete.
It would be good if some elements of the site could be used on business cards and invoices to keep the company identity.
Velirox is a new development company specialized in green energy and sustainable development. We do design, engineering, manufacturing, sourcing and other processes related to product development – both as consultants and for own products.
Keep the look of the site as professional as possible, and with a cooperate-looking style.

Link to existing page: www.velirox.com

Brief Update : After reviewing the designs we would like all new and current designers to make more bold designs that stands out from the rest. We do not like the standard layout that looks like any other cooperate homepage. We want a very unique and very lively page - with faded images and effects when hoovering like seen on our existing page. Try make all elements blend together, and use faded background images instead of just white color - or something else.

Make the site unique !

Industry/Entity Type

Solar Energy

Contact Information for Business Card

Owner/Founder/CEO : Jonas Ulfkær Lindholm
Company name: Velirox ApS
Email: jonas.ulfkaer@velirox.dk
Phone: +45 71 82 64 93
Slogan Sustainable Development
Address: Kildevej 58, 2
DK-5700 Svendborg, Denmark

Number of Pages Required

3 page

Font styles to use
Serif
Sans Serif

Colors
0555a3
85acd3
cedeed
3176b5
cee9f5
85cae6
0293ce
86cfc6
33b8a4

```html
<!DOCTYPE html>
<html lang="en">
<head>
<meta charset="utf-8">
<title>Velirox – Sustainable Development</title>
<link href="https://fonts.googleapis.com/css2?family=Open+Sans:wght@300;400;600;700&display=swap" rel="stylesheet">
<style>
:root{
  --blue:#0293ce;
  --blue-dark:#0555a3;
  --blue-mid:#3176b5;
  --blue-soft:#85acd3;
  --blue-pale:#cedeed;
  --ink:#333;
  --muted:#777;
  --line:#e3e3e3;
  --footer:#1e1f21;
}
*{box-sizing:border-box;margin:0;padding:0}
html,body{width:692px;height:1200px;overflow:hidden}
body{font-family:"Open Sans",Arial,sans-serif;color:var(--ink);background:#fff;position:relative}

/* header */
.site-header{height:64px;display:flex;align-items:center;justify-content:space-between;padding:0 20px 0 26px}
.brand-name{font-size:22px;font-weight:400;color:var(--blue-dark);line-height:1}
.main-nav{display:flex;gap:20px;font-size:7.5px;font-weight:600;color:#555;letter-spacing:.4px}
.main-nav a{color:inherit;text-decoration:none;padding:6px 2px}
.main-nav a.active{color:var(--blue);border-bottom:2px solid var(--blue)}

/* hero */
.hero{position:relative;height:320px;
  background:linear-gradient(115deg,#1c3f73 0%,#2f5d98 30%,#5f95cf 48%,#a9cfee 60%,#d5e9f6 70%,#7fae4e 86%,#4f8a2f 100%)}
.hero-caption{position:absolute;left:56px;top:160px;width:390px;padding:6px 12px;background:rgba(10,25,45,.72);color:#fff;font-size:17px;line-height:1.35;font-weight:400}
.hero-arrow{position:absolute;top:150px;width:18px;height:26px;background:rgba(255,255,255,.75);display:flex;align-items:center;justify-content:center}
.hero-arrow.prev{left:0}.hero-arrow.next{right:0}

/* welcome */
.welcome{text-align:center;padding:44px 60px 0}
.welcome h1{font-size:25px;font-weight:400;color:#222}
.welcome h1 span{color:var(--blue)}
.welcome p{font-size:6.6px;line-height:1.65;color:var(--muted);margin:10px auto 0;max-width:560px}
.btn{display:inline-block;margin-top:14px;background:var(--blue);color:#fff;font-size:6.5px;font-weight:600;padding:6px 16px;letter-spacing:.5px}

/* services */
.services{position:absolute;top:549px;left:0;width:692px;height:205px;
  background:linear-gradient(180deg,#5d8fb6 0%,#86afd0 45%,#b8d2e6 100%);
  display:flex;justify-content:center;gap:14px;padding-top:30px}
.service{width:145px;text-align:center;color:#fff}
.service-img{height:76px}
.service h3{font-size:8.5px;font-weight:600;letter-spacing:.5px;margin-top:12px}
.service p{font-size:6px;line-height:1.6;margin-top:5px;padding:0 8px}
.img-design{background:linear-gradient(135deg,#e2b23c,#d8443a 40%,#2b5fa8 75%,#f0e3b0)}
.img-engineering{background:linear-gradient(135deg,#8fa3b5,#3e566e 55%,#b9c6d2)}
.img-manufacturing{background:linear-gradient(135deg,#2a1d16,#b95a1c 45%,#f3b347 60%,#3a2c22)}
.img-sourcing{background:linear-gradient(135deg,#1b1d22,#3b3f46 50%,#c5252a 80%)}

/* news + video */
.news-video{position:absolute;top:776px;left:40px;width:612px;display:flex;justify-content:space-between}
.section-title{font-size:18px;font-weight:400;color:#222}
.section-title span{color:var(--blue)}
.news{width:370px}
.news-list{display:flex;gap:18px;margin-top:18px;padding-top:14px;border-top:1px solid var(--line)}
.news-item{display:flex;gap:10px;width:176px}
.news-date{text-align:center;color:var(--blue)}
.news-date b{display:block;font-size:20px;font-weight:300;line-height:1}
.news-date small{display:block;font-size:6px;color:#555;font-weight:600;margin-top:3px}
.news-item p{font-size:6px;line-height:1.6;color:var(--muted)}
.news-item a{display:block;font-size:6px;color:var(--blue);text-decoration:none;margin-top:3px}
.video{width:200px}
.video-frame{margin-top:8px;border:1px solid var(--line);padding:6px;box-shadow:0 1px 3px rgba(0,0,0,.12)}
.video-thumb{height:98px;background:linear-gradient(135deg,#dfe6ee,#5b88b8 45%,#f2f4f6);display:flex;align-items:center;justify-content:center}

/* work */
.work{position:absolute;top:990px;left:0;width:692px}
.work .section-title{margin-left:40px}
.work-row{display:flex;gap:12px;margin:16px 0 0 44px}
.work-img{width:190px;height:85px}
.img-tablet{background:linear-gradient(135deg,#f0f0f0,#3a3442 40%,#7c5ea6 60%,#e9e9e9)}
.img-hands{background:linear-gradient(135deg,#7a3a16,#c77a3c 50%,#5a2a0f)}
.img-lab{background:linear-gradient(135deg,#bcd9ee,#5d93c9 50%,#e7f0f7)}
.work-arrow{position:absolute;top:102px;width:16px;height:22px;background:#e8e8e8;display:flex;align-items:center;justify-content:center}
.work-arrow.prev{left:0}.work-arrow.next{right:0}

/* footer */
.site-footer{position:absolute;bottom:0;left:0;width:692px;height:50px;background:var(--footer);display:flex;align-items:center;justify-content:space-between;padding:0 28px;color:#aaa;font-size:6px}
.social{display:flex;gap:5px}
.social i{width:12px;height:12px;border-radius:50%;background:#fff;display:block}
</style>
</head>
<body>

<header class="site-header">
  <div class="brand-name">Velirox</div>
  <nav class="main-nav">
    <a class="active" href="#">HOME</a><a href="#">WEB</a><a href="#">EXPERTISE</a><a href="#">APPROACH</a><a href="#">CLIENTS</a><a href="#">ABOUT</a><a href="#">CONTACT</a>
  </nav>
</header>

<section class="hero" role="img" aria-label="Solar panels beneath a blue sky beside a green lawn and trees">
  <span class="hero-arrow prev"><svg width="6" height="10"><path d="M5 1 1 5l4 4" stroke="#555" fill="none" stroke-width="1.5"/></svg></span>
  <span class="hero-arrow next"><svg width="6" height="10"><path d="M1 1l4 4-4 4" stroke="#555" fill="none" stroke-width="1.5"/></svg></span>
  <div class="hero-caption">Velirox is a new development company<br>specialised in green energy...</div>
</section>

<section class="welcome">
  <h1>Welcome to our <span>site..</span></h1>
  <p>Sed ut perspiciatis unde omnis iste natus error sit voluptatem accusantium doloremque laudantium, totam rem aperiam, eaque ipsa quae ab illo inventore veritatis et quasi architecto beatae vitae dicta sunt explicabo. Nemo enim ipsam voluptatem quia voluptas sit aspernatur aut odit aut fugit, sed quia consequuntur magni dolores eos qui ratione voluptatem sequi nesciunt.</p>
  <span class="btn">READ MORE</span>
</section>

<section class="services">
  <div class="service"><div class="service-img img-design" role="img" aria-label="Colourful design swatches"></div><h3>DESIGN</h3><p>Nemo enim ipsam voluptatem quia voluptas sit aspernatur aut odit aut fugit, sed quia nesciunt.</p></div>
  <div class="service"><div class="service-img img-engineering" role="img" aria-label="Engineering gears and machinery"></div><h3>ENGINEERING</h3><p>Nemo enim ipsam voluptatem quia voluptas sit aspernatur aut odit aut fugit, sed quia nesciunt.</p></div>
  <div class="service"><div class="service-img img-manufacturing" role="img" aria-label="Manufacturing with sparks from metal work"></div><h3>MANUFACTURING</h3><p>Nemo enim ipsam voluptatem quia voluptas sit aspernatur aut odit aut fugit, sed quia nesciunt.</p></div>
  <div class="service"><div class="service-img img-sourcing" role="img" aria-label="Keyboard with a red open source key"></div><h3>SOURCING</h3><p>Nemo enim ipsam voluptatem quia voluptas sit aspernatur aut odit aut fugit, sed quia nesciunt.</p></div>
</section>

<section class="news-video">
  <div class="news">
    <h2 class="section-title">Latest <span>News</span></h2>
    <div class="news-list">
      <article class="news-item"><div class="news-date"><b>02</b><small>AUG 15</small></div><div><p>Nemo enim ipsam voluptatem quia voluptas sit aspernatur aut odit aut fugit sed quia consequuntur magni dolores.</p><a href="#">read more</a></div></article>
      <article class="news-item"><div class="news-date"><b>07</b><small>AUG 15</small></div><div><p>Nemo enim ipsam voluptatem quia voluptas sit aspernatur aut odit aut fugit sed quia consequuntur magni dolores.</p><a href="#">read more</a></div></article>
    </div>
  </div>
  <div class="video">
    <h2 class="section-title">Project <span>Video's</span></h2>
    <div class="video-frame">
      <div class="video-thumb" role="img" aria-label="Project video preview">
        <svg width="26" height="26" viewBox="0 0 26 26"><circle cx="13" cy="13" r="13" fill="#222"/><path d="M10 8l8 5-8 5z" fill="#fff"/></svg>
      </div>
    </div>
  </div>
</section>

<section class="work">
  <h2 class="section-title">Our <span>Work</span></h2>
  <div class="work-row">
    <div class="work-img img-tablet" role="img" aria-label="Tablet device project"></div>
    <div class="work-img img-hands" role="img" aria-label="Hands working on a product"></div>
    <div class="work-img img-lab" role="img" aria-label="Laboratory testing equipment"></div>
  </div>
  <span class="work-arrow prev"><svg width="6" height="10"><path d="M5 1 1 5l4 4" stroke="#666" fill="none" stroke-width="1.5"/></svg></span>
  <span class="work-arrow next"><svg width="6" height="10"><path d="M1 1l4 4-4 4" stroke="#666" fill="none" stroke-width="1.5"/></svg></span>
</section>

<footer class="site-footer">
  <span>Copyright (c) 2015 Velirox. All Right Reserved</span>
  <div class="social"><i></i><i></i><i></i><i></i><i></i><i></i></div>
</footer>

</body>
</html>
```